Google Form Graphic to suit our Brand and industry

Create a graphic / image for us to put at the top of our client enquiry google form.
The image will be a section of an architectural home with our branding over the top. Preferably translucent.
The image must suit the shape of the google forms image, which is an elongated rectangle
#003d5d - brand colour

Target Market(s)

residential home owners, high end architectural homes

Industry/Entity Type

Residential construction

Colors
0054AA
0677BA
7BADD7
CADEEF
E8F1F8

Requirements
Must have
• our branding and a photo of an architectural home in the background

```html
<!DOCTYPE html>
<html lang="en">
<head>
<meta charset="utf-8">
<title>Orin Builds – Form Header Options</title>
<link href="https://fonts.googleapis.com/css2?family=Poppins:wght@400&display=swap" rel="stylesheet">
<style>
  :root {
    --page: #ffffff;
    --ink: #1a1a1a;
    --brand: #0054aa;
    --brand-deep: #003d5d;
    --brand-mid: #0677ba;
    --wood: #b5652c;
    --wood-dark: #7a3d18;
    --sky: #e6e8e8;
    --foliage: #4d6a3a;
    --white: #ffffff;
  }
  * { box-sizing: border-box; margin: 0; padding: 0; }
  html, body {
    width: 1200px;
    height: 1114px;
    overflow: hidden;
    background: var(--page);
  }
  .sheet {
    position: relative;
    width: 1200px;
    height: 1114px;
  }
  .option-label {
    position: absolute;
    left: 197px;
    font-family: "Poppins", sans-serif;
    font-size: 11px;
    letter-spacing: 0.32em;
    color: var(--ink);
  }
  .banner {
    position: absolute;
    left: 198px;
    width: 823px;
    overflow: hidden;
  }
  .banner-photo {
    position: absolute;
    inset: 0;
    background:
      linear-gradient(180deg, rgba(0,0,0,0) 55%, rgba(60,30,10,0.35) 100%),
      linear-gradient(100deg,
        var(--foliage) 0%,
        #5a5a3a 28%,
        var(--wood-dark) 40%,
        var(--wood) 58%,
        #c9773a 75%,
        #9a7a55 88%,
        var(--sky) 100%);
  }
  .banner-photo::before {
    content: "";
    position: absolute;
    left: 0; right: 0; top: 0;
    height: 38%;
    background: linear-gradient(90deg, rgba(230,232,232,0) 30%, rgba(230,232,232,0.35) 100%),
                linear-gradient(180deg, #c5762f 0%, rgba(181,101,44,0) 100%);
  }
  .banner-overlay {
    position: absolute;
    inset: 0;
    width: 100%;
    height: 100%;
  }
  .banner-overlay polygon {
    fill: var(--brand-mid);
    opacity: 0.82;
  }
  .wordmark {
    position: absolute;
    font-family: "Poppins", sans-serif;
    font-weight: 400;
    color: var(--white);
    white-space: nowrap;
    line-height: 1;
    transform: translateY(-50%);
  }
  .option-a { top: 116px; height: 211px; }
  .option-b { top: 472px; height: 205px; }
  .option-c { top: 831px; height: 206px; left: 199px; width: 822px; }

  .option-a .wordmark { left: 96px; top: 105px; font-size: 25px; letter-spacing: 0.42em; }
  .option-b .wordmark { left: 120px; top: 103px; font-size: 38px; letter-spacing: 0.42em; }
  .option-c .wordmark { left: 121px; top: 104px; font-size: 52px; letter-spacing: 0.44em; }
</style>
</head>
<body>
<main class="sheet">

  <p class="option-label" style="top:86px">OPTIONS A</p>
  <section class="banner option-a">
    <div class="banner-photo" role="img" aria-label="Photo of a timber architectural home with slatted screens and a landscape beyond"></div>
    <svg class="banner-overlay" viewBox="0 0 823 211" preserveAspectRatio="none" aria-hidden="true">
      <polygon points="0,0 266,0 186,105 275,211 0,211"/>
    </svg>
    <span class="wordmark">ORIN BUILDS</span>
  </section>

  <p class="option-label" style="top:443px">OPTIONS B</p>
  <section class="banner option-b">
    <div class="banner-photo" role="img" aria-label="Photo of a timber architectural home with slatted screens and a landscape beyond"></div>
    <svg class="banner-overlay" viewBox="0 0 823 205" preserveAspectRatio="none" aria-hidden="true">
      <polygon points="0,0 346,0 276,101 348,205 0,205"/>
    </svg>
    <span class="wordmark">ORIN BUILDS</span>
  </section>

  <p class="option-label" style="top:800px">OPTIONS C</p>
  <section class="banner option-c">
    <div class="banner-photo" role="img" aria-label="Photo of a timber architectural home with slatted screens and a landscape beyond"></div>
    <svg class="banner-overlay" viewBox="0 0 822 206" preserveAspectRatio="none" aria-hidden="true">
      <polygon points="0,0 381,0 322,102 384,206 0,206"/>
    </svg>
    <span class="wordmark">ORIN BUILDS</span>
  </section>

</main>
</body>
</html>
```